​Silver Harbor Rhythm provides personal, friendly service in a fun and high energy environment. We are based in Vermont.

We would like a card that appeals to a wide range of audiences as we do a wide range of events. Please feel free to check out our website silverharborrhythm.net for inspiration.

Target Market(s)

weddings, corporate, birthday parties, colleges

Industry/Entity Type

Business

Contact Information for Business Card

Silver Harbor Rhythm
Providing Entertainment For All Occasions
555 274 9160
silverharborrhythm@mailnest.net
silverharborrhythm.net

```html
<!DOCTYPE html>
<html lang="en">
<head>
<meta charset="utf-8">
<title>Silver Harbor Rhythm — Business Card</title>
<link rel="stylesheet" href="https://fonts.googleapis.com/css2?family=Montserrat:wght@700&family=Open+Sans:wght@400;700&display=swap">
<style>
  :root {
    --stage: #e9e6e1;
    --paper: #ffffff;
    --forest: #2b5a12;
    --ink: #111111;
    --slate: #555555;
    --shadow: rgba(0, 0, 0, 0.18);
  }
  html, body {
    margin: 0;
    padding: 0;
    width: 1200px;
    height: 829px;
    overflow: hidden;
    background: var(--stage);
  }
  .canvas {
    position: relative;
    width: 1200px;
    height: 829px;
  }
  .card {
    position: absolute;
    width: 540px;
    height: 310px;
    background: var(--paper);
    box-shadow: 0 8px 24px var(--shadow);
    overflow: hidden;
    font-family: "Open Sans", Arial, sans-serif;
  }
  .card--front { left: 50px; top: 230px; }
  .card--back { left: 610px; top: 290px; }

  .front-swoosh {
    position: absolute;
    inset: 0;
  }
  .brand {
    font-family: "Montserrat", Arial, sans-serif;
    font-weight: 700;
    color: var(--forest);
    letter-spacing: 0.5px;
    display: flex;
    align-items: center;
    gap: 8px;
  }
  .brand-mark {
    width: 14px;
    height: 14px;
    background: var(--forest);
    border-radius: 50%;
    flex: none;
  }
  .card--front .brand {
    position: absolute;
    left: 34px;
    top: 92px;
    font-size: 17px;
  }
  .holder {
    position: absolute;
    left: 34px;
    top: 160px;
    font-size: 15px;
    color: var(--forest);
  }
  .holder strong { font-weight: 700; }
  .address {
    position: absolute;
    left: 34px;
    top: 198px;
    font-size: 13px;
    line-height: 21px;
    color: var(--slate);
  }
  .contact {
    position: absolute;
    right: 16px;
    top: 34px;
    margin: 0;
    padding: 0;
    list-style: none;
    color: var(--paper);
    font-size: 10.5px;
    line-height: 19px;
    text-align: right;
  }
  .contact li {
    display: flex;
    justify-content: flex-end;
    align-items: center;
    gap: 5px;
  }
  .contact svg { width: 10px; height: 10px; flex: none; }

  .card--back .brand {
    position: absolute;
    left: 0;
    right: 0;
    top: 118px;
    justify-content: center;
    font-size: 24px;
  }
  .card--back .brand-mark { width: 18px; height: 18px; }
  .site {
    position: absolute;
    left: 0;
    right: 0;
    top: 180px;
    text-align: center;
    font-size: 16px;
    letter-spacing: 0.8px;
    color: #333333;
  }
</style>
</head>
<body>
<main class="canvas">

  <section class="card card--front" aria-label="Business card front">
    <svg class="front-swoosh" viewBox="0 0 540 310" width="540" height="310" aria-hidden="true">
      <path d="M255,0 L290,0 C380,70 445,190 470,310 L455,310 C430,190 360,70 255,0 Z" fill="var(--ink)"/>
      <path d="M290,0 L540,0 L540,310 L470,310 C445,190 380,70 290,0 Z" fill="var(--forest)"/>
    </svg>

    <div class="brand"><span class="brand-mark"></span>SILVER HARBOR RHYTHM</div>

    <p class="holder" style="margin:0"><strong>Your Name,</strong> Title</p>
    <p class="address" style="margin:0">Sreet Name, City Name<br>Zip Code-00000</p>

    <ul class="contact">
      <li>
        <svg viewBox="0 0 10 10" aria-hidden="true"><path d="M2 0.5 L3.8 2.6 L2.9 3.7 C3.6 5 4.9 6.3 6.3 7.1 L7.4 6.2 L9.5 8 L8.2 9.5 C4.3 9 1 5.7 0.5 1.8 Z" fill="currentColor"/></svg>
        555 274 9160
      </li>
      <li>
        <svg viewBox="0 0 10 10" aria-hidden="true"><rect x="0.5" y="2" width="9" height="6.5" rx="1" fill="none" stroke="currentColor"/><path d="M0.8 2.4 L5 5.6 L9.2 2.4" fill="none" stroke="currentColor"/></svg>
        silverharborrhythm@mailnest.net
      </li>
      <li>
        <svg viewBox="0 0 10 10" aria-hidden="true"><circle cx="5" cy="5" r="4.4" fill="none" stroke="currentColor"/><ellipse cx="5" cy="5" rx="1.9" ry="4.4" fill="none" stroke="currentColor"/><path d="M0.6 5 H9.4" stroke="currentColor"/></svg>
        www.silverharborrhythm.net
      </li>
    </ul>
  </section>

  <section class="card card--back" aria-label="Business card back">
    <div class="brand"><span class="brand-mark"></span>SILVER HARBOR RHYTHM</div>
    <p class="site" style="margin:0">www.silverharborrhythm.net</p>
  </section>

</main>
</body>
</html>
```